Corporate Business Card

Very professional, Modern, Not to busy, include phone address email, website
(253) 617-4930, 18761 52nd Avenue S, Kent, WA 98047, martin@plumlinegroup.com, varkoworks.com

Target Market(s)

Manufacturing

Industry/Entity Type

Aero, machining, manufacturing, Off road racing

Contact Information for Business Card

Phone, address email, website

```html
<!DOCTYPE html>
<html lang="en">
<head>
<meta charset="UTF-8">
<title>Varko Works — Business Card Front</title>
<link rel="stylesheet" href="https://fonts.googleapis.com/css2?family=Exo+2:wght@400;800&display=swap">
<style>
  :root {
    --card-navy: #17346c;
    --card-red: #d2232a;
    --card-white: #ffffff;
    --card-white-soft: rgba(255, 255, 255, 0.88);
  }
  html, body {
    margin: 0;
    padding: 0;
    width: 1200px;
    height: 685px;
    overflow: hidden;
    background: var(--card-navy);
  }
  .card-front {
    position: relative;
    width: 1200px;
    height: 685px;
    background: var(--card-navy);
    overflow: hidden;
  }
  .accent-wedge {
    position: absolute;
    inset: 0;
    width: 1200px;
    height: 685px;
  }
  .accent-wedge polygon {
    fill: var(--card-red);
  }
  .brand-name {
    position: absolute;
    left: 474px;
    top: 262px;
    width: 531px;
    margin: 0;
    font-family: "Exo 2", "Arial Black", sans-serif;
    font-weight: 800;
    font-size: 74px;
    line-height: 1;
    letter-spacing: 2px;
    text-transform: uppercase;
    text-align: center;
    color: var(--card-white);
    white-space: nowrap;
  }
  .contact-list {
    position: absolute;
    left: 474px;
    top: 392px;
    width: 531px;
    margin: 0;
    padding: 0;
    list-style: none;
    font-family: "Exo 2", Arial, sans-serif;
    font-weight: 400;
    font-size: 21px;
    line-height: 32px;
    letter-spacing: 0.5px;
    text-align: center;
    color: var(--card-white-soft);
    white-space: nowrap;
  }
</style>
</head>
<body>
  <main class="card-front">
    <svg class="accent-wedge" viewBox="0 0 1200 685" aria-hidden="true">
      <polygon points="0,0 474,0 108,685 0,685"/>
    </svg>
    <h1 class="brand-name">Varko Works</h1>
    <ul class="contact-list">
      <li class="contact-phone">(253) 617-4930</li>
      <li class="contact-address">18761 52nd Avenue S, Kent, WA 98047</li>
      <li class="contact-email">martin@plumlinegroup.com</li>
      <li class="contact-web">varkoworks.com</li>
    </ul>
  </main>
</body>
</html>
```